Marketing - Outdoor Vinyl banner, Outdoor Poster, Flyer modifications

Hi, I worked with you in the past and attached flyer designs. It just needs to be tweaked for various prints.
1)Outdoor vinyl banner (4 feet height and 8 feet width) print: Just grand opening pic, logo with name, tagline and call/text us portion.
2)Outdoor Poster (5 feet height and 3 feet width) print: same as above
3) Indoor poster for both horizontal & Vertical prints: Just logo w/ name, tagline, "We are MOVING Next door"
4)Flyer: will give minor modifications to attached flyer designs

```html
<!DOCTYPE html>
<html lang="en">
<head>
<meta charset="utf-8">
<title>Brightarc Dental – Grand Opening &amp; Moving Set</title>
<link rel="stylesheet" href="https://fonts.googleapis.com/css2?family=Oswald:wght@600&family=Montserrat:wght@600;700;900&family=Poppins:wght@600;700&family=Playfair+Display:wght@400;900&display=swap">
<style>
  :root{
    --cyan:#0fb0d8;
    --cyan-deep:#0a9cc4;
    --slate:#5f7a96;
    --slate-dark:#495f78;
    --ink:#3e4f63;
    --white:#ffffff;
    --backdrop:#e2e4e6;
    --photo-a:#d9c2b0;
    --photo-b:#7f93ab;
  }
  *{box-sizing:border-box;margin:0;padding:0}
  html,body{width:1200px;height:480px;overflow:hidden;background:var(--backdrop)}
  .sheet{position:relative;width:1200px;height:480px}
  .piece{position:absolute;background:var(--white);overflow:hidden;box-shadow:0 3px 10px rgba(0,0,0,.18)}
  .banner{left:99px;top:15px;width:451px;height:225px}
  .sign-wide{left:99px;top:257px;width:345px;height:210px}
  .poster{left:565px;top:16px;width:267px;height:444px}
  .sign-tall{left:851px;top:17px;width:270px;height:443px}
  .waves{position:absolute;left:0;top:0;width:100%;height:100%}

  .brand{position:absolute;display:flex;align-items:center;gap:5px;
    font-family:"Montserrat",sans-serif;font-weight:700;color:var(--cyan);letter-spacing:.03em;white-space:nowrap;z-index:2}
  .brand-dot{display:inline-block;border-radius:50%;background:var(--cyan);flex:none}

  .photo{position:absolute;background:linear-gradient(135deg,var(--photo-a) 0%,#c8b3a5 45%,var(--photo-b) 100%)}
  .balloons{position:absolute;background:linear-gradient(180deg,#e8a1a8 0%,#f6cf8d 50%,#9ed9e6 100%);opacity:.75;border-radius:40px}

  .headline-box{position:absolute;background:var(--slate);border:2px solid var(--cyan);border-radius:4px;
    color:var(--white);text-align:center;outline:2px solid var(--white);outline-offset:-4px;z-index:2}
  .banner .headline-box{left:17px;top:18px;width:233px;height:42px;
    font-family:"Oswald",sans-serif;font-weight:600;font-size:29px;line-height:38px;letter-spacing:.02em}
  .poster .headline-box{left:31px;top:63px;width:204px;height:63px;
    font-family:"Montserrat",sans-serif;font-weight:900;font-size:28px;line-height:27px;padding-top:5px}

  .call-label{position:absolute;left:18px;top:74px;font-family:"Poppins",sans-serif;font-weight:700;font-size:15px;color:var(--ink)}
  .phone-pill{position:absolute;display:flex;border-radius:5px;overflow:hidden;background:var(--cyan);
    font-family:"Poppins",sans-serif;font-weight:600;color:var(--white);z-index:2}
  .phone-icon{display:flex;align-items:center;justify-content:center;background:var(--slate-dark)}
  .phone-number{flex:1;text-align:center;letter-spacing:.05em}
  .banner .phone-pill{left:17px;top:98px;width:165px;height:23px}
  .banner .phone-icon{width:31px}
  .banner .phone-number{font-size:16px;line-height:23px}
  .poster .phone-pill{left:20px;top:363px;width:234px;height:32px}
  .poster .phone-icon{width:45px}
  .poster .phone-number{font-size:24px;line-height:32px}
  .hours{position:absolute;font-family:"Poppins",sans-serif;font-weight:600;color:var(--slate)}
  .banner .hours{left:20px;top:135px;font-size:7px}
  .poster .hours{left:0;width:100%;text-align:center;top:400px;font-size:11px}
  .welcome{position:absolute;left:0;width:100%;text-align:center;top:416px;
    font-family:"Poppins",sans-serif;font-weight:700;font-size:14px;color:var(--cyan)}

  .serif{position:absolute;left:0;width:100%;text-align:center;color:var(--white);font-family:"Playfair Display",serif;white-space:nowrap}
  .moving{font-weight:400}
  .next-door{font-weight:900;letter-spacing:-.01em}
  .tagline{font-weight:400}
  .sign-wide .moving{top:95px;font-size:27px}
  .sign-wide .next-door{top:120px;font-size:48px;line-height:1.1}
  .sign-wide .tagline{top:180px;font-size:20px}
  .sign-tall .moving{top:145px;font-size:30px}
  .sign-tall .next-door{top:190px;font-size:72px;line-height:1}
  .sign-tall .next-door.second{top:262px;font-size:74px}
  .sign-tall .tagline{top:393px;font-size:17px}
</style>
</head>
<body>
<div class="sheet">

  <!-- Outdoor vinyl banner -->
  <section class="piece banner">
    <div class="balloons" role="img" aria-label="Colourful party balloons" style="left:414px;top:0;width:37px;height:150px"></div>
    <div class="balloons" role="img" aria-label="Colourful party balloons" style="left:-20px;top:45px;width:34px;height:120px"></div>
    <div class="photo" role="img" aria-label="Smiling family of four giving thumbs up" style="left:170px;top:62px;width:244px;height:163px"></div>
    <svg class="waves" viewBox="0 0 451 225" preserveAspectRatio="none" aria-hidden="true">
      <path d="M0 185 C60 150 120 150 190 180 C260 210 330 230 451 195 L451 225 L0 225Z" fill="var(--white)"/>
      <path d="M0 190 C50 150 110 140 180 170 C250 205 330 225 451 185 L451 195 C330 235 250 220 180 185 C110 155 55 165 0 205Z" fill="var(--cyan)"/>
      <path d="M240 200 C320 215 390 200 451 175 L451 188 C390 212 320 222 240 200Z" fill="var(--slate)"/>
    </svg>
    <div class="headline-box">GRAND OPENING</div>
    <div class="brand" style="left:272px;top:30px;font-size:11px"><span class="brand-dot" style="width:10px;height:10px"></span>BRIGHTARC DENTAL</div>
    <div class="call-label">Call or Text Us Now:</div>
    <div class="phone-pill">
      <span class="phone-icon"><svg width="12" height="12" viewBox="0 0 24 24"><path fill="#fff" d="M6.6 10.8a15 15 0 0 0 6.6 6.6l2.2-2.2a1 1 0 0 1 1-.25 11.4 11.4 0 0 0 3.6.57 1 1 0 0 1 1 1V20a1 1 0 0 1-1 1A17 17 0 0 1 3 4a1 1 0 0 1 1-1h3.5a1 1 0 0 1 1 1c0 1.250.2 2.450.57 3.570a1 1 0 0 1-.25 1z"/></svg></span>
      <span class="phone-number">555.014.2288</span>
    </div>
    <div class="hours">Convenient Evening &amp; Saturday Hours</div>
  </section>

  <!-- Indoor horizontal sign -->
  <section class="piece sign-wide">
    <svg class="waves" viewBox="0 0 345 210" preserveAspectRatio="none" aria-hidden="true">
      <path d="M0 58 C60 95 130 95 200 70 C260 50 300 48 345 50 L345 210 L0 210Z" fill="var(--slate)"/>
      <path d="M0 75 C70 100 140 95 210 78 C270 64 310 62 345 62 L345 210 L0 210Z" fill="var(--cyan)"/>
      <path d="M0 188 C100 170 240 168 345 180 L345 210 L0 210Z" fill="var(--white)"/>
      <path d="M0 192 C100 175 240 173 345 185 L345 210 L0 210Z" fill="var(--slate)"/>
    </svg>
    <div class="brand" style="left:84px;top:26px;font-size:16px"><span class="brand-dot" style="width:13px;height:13px"></span>BRIGHTARC DENTAL</div>
    <div class="serif moving">We’re MOVING</div>
    <div class="serif next-door">Next DOOR!</div>
    <div class="serif tagline">Exciteed to find home!</div>
  </section>

  <!-- Outdoor poster -->
  <section class="piece poster">
    <div class="balloons" role="img" aria-label="Colourful party balloons" style="left:0;top:48px;width:48px;height:150px"></div>
    <div class="balloons" role="img" aria-label="Colourful party balloons" style="left:225px;top:48px;width:42px;height:150px"></div>
    <div class="photo" role="img" aria-label="Smiling family of four giving thumbs up" style="left:0;top:130px;width:267px;height:210px"></div>
    <svg class="waves" viewBox="0 0 267 444" preserveAspectRatio="none" aria-hidden="true">
      <path d="M0 330 C60 300 120 345 180 345 C220 345 245 335 267 320 L267 444 L0 444Z" fill="var(--white)"/>
      <path d="M100 330 C150 360 220 355 267 315 L267 325 C220 362 150 368 100 330Z" fill="var(--slate)"/>
      <path d="M90 340 C150 372 220 365 267 330 L267 336 C220 372 150 380 90 340Z" fill="var(--cyan)"/>
    </svg>
    <div class="brand" style="left:64px;top:30px;font-size:12px"><span class="brand-dot" style="width:11px;height:11px"></span>BRIGHTARC DENTAL</div>
    <div class="headline-box">GRAND<br>OPENING</div>
    <div class="phone-pill">
      <span class="phone-icon"><svg width="18" height="18" viewBox="0 0 24 24"><path fill="#fff" d="M6.6 10.8a15 15 0 0 0 6.6 6.6l2.2-2.2a1 1 0 0 1 1-.25 11.4 11.4 0 0 0 3.6.57 1 1 0 0 1 1 1V20a1 1 0 0 1-1 1A17 17 0 0 1 3 4a1 1 0 0 1 1-1h3.5a1 1 0 0 1 1 1c0 1.250.2 2.450.57 3.570a1 1 0 0 1-.25 1z"/></svg></span>
      <span class="phone-number">555.014.2288</span>
    </div>
    <div class="hours">Convenient Evening &amp; Saturday Hours</div>
    <div class="welcome">New patients are welcome!</div>
  </section>

  <!-- Indoor vertical sign -->
  <section class="piece sign-tall">
    <svg class="waves" viewBox="0 0 270 443" preserveAspectRatio="none" aria-hidden="true">
      <path d="M0 90 C60 120 100 80 160 76 C200 73 240 82 270 100 L270 443 L0 443Z" fill="var(--slate)"/>
      <path d="M0 112 C60 135 110 100 170 96 C210 94 245 100 270 112 L270 443 L0 443Z" fill="var(--cyan)"/>
      <path d="M0 443 C30 395 80 355 135 354 C190 355 245 395 270 443Z" fill="var(--white)"/>
      <path d="M6 443 C35 402 82 363 135 362 C188 363 240 402 264 443Z" fill="var(--slate)"/>
    </svg>
    <div class="brand" style="left:44px;top:50px;font-size:15px"><span class="brand-dot" style="width:12px;height:12px"></span>BRIGHTARC DENTAL</div>
    <div class="serif moving">We’re MOVING</div>
    <div class="serif next-door">Next</div>
    <div class="serif next-door second">DOOR!</div>
    <div class="serif tagline">Exciteed to find home!</div>
  </section>

</div>
</body>
</html>
```